Professional Personal Website with Blog and four sections

I am seeking a website design for myself. I would like the site to contain a blog, related to Information Security and several sections.

I am an established Information Security Consultant (one aspect of the site).
I am an author of a children's spiritual book that is "new thought" (another aspect of the site)
I am a co-founder of a secure social platform for kids and families (www.bramlowt.com)
I may want a section on finance as well, not sure at this moment

I want this site to be a personal website, not a subscription service or professional services sales site, I want the site to look very professional, so that I can share it with all types of people without concern - business, spiritual, other.

I have provided a photo of myself for the site, smart casual on a beach. The site will be hosted on dorianhelpe.com

You can see samples of what I am referring to by searching "personal website" on images.zentrova.com

I would like the page layout, and the images chopped up as individual jpgs, including hover images for buttons. I can do the coding

I would like the following buttons
Home, About, Information Security Blog, Passion Projects, Contact

I would like the top portion of the page to say "Tobin Marsh"
I would like the subtext to say:
Executive Information Security Architect, Author, and Idea Man

I envision the following

Target Market(s)

Executive / Technical / Creative types / Spritual types

Number of Pages Required

4 page

Requirements
Must have
• Blog section
Should not have
• No Matrix themes or No Cop themes, No Fingerprints or Eyeball scans

```html
<!DOCTYPE html>
<html lang="en">
<head>
<meta charset="utf-8">
<title>dorianhelpe — Information Security Consultant</title>
<link href="https://fonts.googleapis.com/css2?family=Roboto:wght@400;500;700;900&display=swap" rel="stylesheet">
<style>
:root{
  --navy:#0f2f66;
  --nav:#163d7c;
  --nav-active:#3d5f9a;
  --blue:#1d4f9e;
  --text:#333;
  --muted:#777;
  --rule:#ddd;
  --page:#f2f2f2;
  --footer:#e9e9e9;
  --footer-bar:#1a3d78;
}
*{box-sizing:border-box;margin:0;padding:0}
html,body{width:1200px;height:2204px;overflow:hidden}
body{font-family:"Roboto",Arial,sans-serif;color:var(--text);background:var(--page);position:relative}
.abs{position:absolute}

/* header */
.site-header{left:0;top:0;width:1200px;height:120px;background:#fff}
.brand{left:40px;top:34px;display:flex;align-items:center;gap:14px}
.brand-mark{width:40px;height:40px;border-radius:50%;background:var(--blue)}
.brand-name{font-size:36px;font-weight:500;color:var(--navy);letter-spacing:-.5px}
.search{left:600px;top:44px;display:flex}
.search-field{width:236px;height:34px;border:1px solid #ccc;font-size:13px;color:#999;padding:8px 10px}
.search-btn{width:44px;height:34px;background:var(--navy);display:flex;align-items:center;justify-content:center}
.call{left:964px;top:36px;display:flex;gap:12px;align-items:center}
.call-icon{width:42px;height:42px;border-radius:50%;border:2px solid var(--navy);display:flex;align-items:center;justify-content:center}
.call-text small{display:block;font-size:15px;color:var(--muted)}
.call-text strong{font-size:20px;color:var(--navy)}

/* nav */
.main-nav{left:0;top:120px;width:1200px;height:40px;background:var(--nav);display:flex;padding-left:36px}
.main-nav a{color:#fff;text-decoration:none;font-size:13px;font-weight:500;width:130px;text-align:center;line-height:40px;letter-spacing:.5px}
.main-nav a.active{background:var(--nav-active)}

/* hero */
.hero{left:0;top:160px;width:1200px;height:500px;background:linear-gradient(120deg,#0c1722 0%,#2a3540 45%,#6b7680 70%,#1c2530 100%)}
.hero-title{left:36px;top:360px;color:#fff;font-size:27px;font-weight:700;line-height:1.25;letter-spacing:.3px}
.hero-title span{font-weight:400}
.hero-btn{left:100px;top:446px;width:140px;height:36px;background:var(--blue);color:#fff;font-size:14px;text-align:center;line-height:36px}
.hero-arrow{top:386px;width:30px;height:30px;border-radius:50%;background:rgba(255,255,255,.25);display:flex;align-items:center;justify-content:center}

/* blog */
.section-title{left:108px;top:702px;font-size:34px;font-weight:700;color:#222}
.post{left:108px;width:692px;height:260px;background:#fff;border:1px solid var(--rule);display:flex;padding:20px}
.post-thumb{width:256px;height:200px;flex:none}
.post-body{padding-left:22px;flex:1}
.post-meta{font-size:11px;color:var(--muted);margin-top:6px}
.post-title{font-size:24px;font-weight:700;color:#222;line-height:1.15;margin:8px 0 10px}
.post-excerpt{font-size:12.5px;line-height:1.5;color:#555}
.post-foot{display:flex;gap:26px;margin-top:12px;font-size:12px;color:var(--muted)}
.post-foot .more{color:var(--navy);font-weight:500}

.pager{left:324px;top:1896px;display:flex;gap:6px}
.pager span{min-width:36px;height:26px;border:1px solid #ccc;background:#fff;font-size:12px;line-height:24px;text-align:center;padding:0 6px}
.pager span.on{background:var(--blue);color:#fff;border-color:var(--blue)}

/* sidebar */
.widget{left:828px;width:272px;background:#fff;border:1px solid var(--rule);padding:16px}
.widget h3{font-size:26px;font-weight:700;color:#222;margin-bottom:8px}
.widget p{font-size:12.5px;color:#555;line-height:1.45}
.video{height:172px;margin:-16px -16px 14px;display:flex;align-items:center;justify-content:center}
.play{width:46px;height:46px;border-radius:50%;background:#fff;display:flex;align-items:center;justify-content:center}
.mini{display:flex;gap:10px;margin-bottom:10px}
.mini-thumb{width:80px;height:52px;flex:none}
.mini b{font-size:12.5px;color:#222;display:block}
.mini small{font-size:11px;color:var(--muted)}
.socials{display:flex;gap:12px;margin:4px 0 14px}
.socials span{width:16px;height:16px;background:#444;border-radius:3px}
.sub{display:flex}
.sub-field{flex:1;height:32px;border:1px solid #ccc;font-size:12px;color:#999;padding:8px}
.sub-btn{width:70px;height:32px;background:var(--navy);color:#fff;font-size:13px;text-align:center;line-height:32px}
.author{display:flex;gap:12px;align-items:center;margin-top:14px}
.author-pic{width:52px;height:52px;border-radius:50%;background:linear-gradient(#8a9bb0,#3d4a5c)}
.author b{font-size:12px;color:var(--navy);display:block}
.author small{font-size:11px;color:var(--muted)}

/* footer */
.site-footer{left:0;top:1960px;width:1200px;height:200px;background:var(--footer);padding:24px 40px;display:flex;gap:60px}
.foot-col h4{font-size:27px;font-weight:500;color:#222;margin-bottom:10px}
.foot-col li{list-style:none;font-size:12.5px;color:#555;line-height:1.75}
.foot-col li::before{content:"› ";color:var(--blue)}
.tags{display:flex;flex-wrap:wrap;gap:6px;width:290px}
.tags span{font-size:12px;color:#555;border:1px solid #bbb;padding:4px 10px;background:#fff}
.foot-bar{left:0;top:2160px;width:1200px;height:44px;background:var(--footer-bar);color:#cfd8e8;font-size:12px;display:flex;align-items:center;justify-content:space-between;padding:0 40px}
.foot-social{display:flex;gap:8px}
.foot-social span{width:26px;height:26px;border-radius:50%;border:1px solid #cfd8e8}
</style>
</head>
<body>

<header class="site-header abs">
  <div class="brand abs"><span class="brand-mark"></span><span class="brand-name">dorianhelpe</span></div>
  <div class="search abs"><div class="search-field">Enter your keywords...</div><div class="search-btn"><svg width="16" height="16" viewBox="0 0 16 16"><circle cx="6.5" cy="6.5" r="4.5" fill="none" stroke="#fff" stroke-width="2"/><line x1="10" y1="10" x2="14" y2="14" stroke="#fff" stroke-width="2"/></svg></div></div>
  <div class="call abs"><div class="call-icon"><svg width="20" height="20" viewBox="0 0 20 20"><path d="M5 2l3 4-2 2c1 2 3 4 5 5l2-2 4 3-2 3C9 17 3 11 2 5z" fill="#0f2f66"/></svg></div><div class="call-text"><small>Call Us Now</small><strong>1-800-555-0142</strong></div></div>
</header>

<nav class="main-nav abs">
  <a class="active">HOME</a><a>ABOUT</a><a>NEWS</a><a>PORTFOLIO</a><a>FEATURES</a><a>CONTACT US</a>
</nav>

<section class="hero abs" role="img" aria-label="Photo of hands working at a laptop keyboard with a magnifying glass"></section>
<h1 class="hero-title abs">INFORMATION SECURITY<br><span>CONSULTANT</span></h1>
<div class="hero-btn abs">View the Details</div>
<div class="hero-arrow abs" style="left:12px"><svg width="12" height="12" viewBox="0 0 12 12"><path d="M8 1L3 6l5 5" stroke="#fff" stroke-width="2" fill="none"/></svg></div>
<div class="hero-arrow abs" style="left:1158px"><svg width="12" height="12" viewBox="0 0 12 12"><path d="M4 1l5 5-5 5" stroke="#fff" stroke-width="2" fill="none"/></svg></div>

<h2 class="section-title abs">OUR BLOG</h2>

<article class="post abs" style="top:752px;height:280px">
  <div class="post-thumb" role="img" aria-label="Photo of a blue digital security screen" style="background:linear-gradient(135deg,#0d2a55,#3d6aa8)"></div>
  <div class="post-body">
    <div class="post-meta">▣ January 12, 2016 by admin</div>
    <h3 class="post-title">Information Security Consultant</h3>
    <p class="post-excerpt">Lorem ipsum is simply dummy text of the printing and typesetting industry. Lorem ipsum has been the industry's standard dummy text ever since the 1500s, when an unknown printer took a galley of type and scrambled it to make a type specimen book. It has survived not only five centuries.</p>
    <div class="post-foot"><span class="more">Continue reading</span><span>Domestic, General</span><span>▢ Add comment</span></div>
  </div>
</article>

<article class="post abs" style="top:1056px">
  <div class="post-thumb" role="img" aria-label="Photo of children reading a book together" style="background:linear-gradient(135deg,#c9b79a,#e8a37a)"></div>
  <div class="post-body">
    <div class="post-meta">▣ January 12, 2016 by admin</div>
    <h3 class="post-title">Children's spiritual book that is new thought</h3>
    <p class="post-excerpt">Lorem ipsum is simply dummy text of the printing and typesetting industry. Lorem ipsum has been the industry's standard dummy text ever since the 1500s, when an unknown printer took a galley of type and scrambled it.</p>
    <div class="post-foot"><span class="more">Continue reading</span><span>Domestic, General</span><span>▢ Add comment</span></div>
  </div>
</article>

<article class="post abs" style="top:1336px">
  <div class="post-thumb" role="img" aria-label="Photo of a family running on a green field" style="background:linear-gradient(180deg,#a8cbe8 0%,#d6e6f0 45%,#7fb24a 55%,#4f8a2a 100%)"></div>
  <div class="post-body">
    <div class="post-meta">▣ January 12, 2016 by admin</div>
    <h3 class="post-title">Secure social platform for kids and families</h3>
    <p class="post-excerpt">Lorem ipsum is simply dummy text of the printing and typesetting industry. Lorem ipsum has been the industry's standard dummy text ever since the 1500s, when an unknown printer took a galley of type and scrambled it.</p>
    <div class="post-foot"><span class="more">Continue reading</span><span>Domestic, General</span><span>▢ Add comment</span></div>
  </div>
</article>

<article class="post abs" style="top:1616px">
  <div class="post-thumb" role="img" aria-label="Photo of a hand writing financial notes beside a calculator" style="background:linear-gradient(135deg,#e8e8e8,#9aa4ae)"></div>
  <div class="post-body">
    <div class="post-meta">▣ January 12, 2016 by admin</div>
    <h3 class="post-title">Financial management</h3>
    <p class="post-excerpt">Lorem ipsum is simply dummy text of the printing and typesetting industry. Lorem ipsum has been the industry's standard dummy text ever since the 1500s, when an unknown printer took a galley of type and scrambled it to make a type specimen book. It has survived five centuries.</p>
    <div class="post-foot"><span class="more">Continue reading</span><span>Domestic, General</span><span>▢ Add comment</span></div>
  </div>
</article>

<div class="pager abs"><span>« Prev</span><span>1</span><span class="on">2</span><span>3</span><span>4</span><span>5</span><span>6</span><span>Next »</span></div>

<aside class="widget abs" style="top:752px">
  <div class="video" role="img" aria-label="Video still of a person in a suit" style="background:linear-gradient(135deg,#5a6470,#c4c9cf)"><div class="play"><svg width="16" height="16" viewBox="0 0 16 16"><path d="M4 2l10 6-10 6z" fill="#1d4f9e"/></svg></div></div>
  <h3>Latest video</h3>
  <p>Lorem ipsum is simply dummy text of the printing and typesetting industry. Lorem ipsum has been dummy text.</p>
  <p style="color:#0f2f66;font-weight:500;margin-top:6px">Continue reading</p>
</aside>

<aside class="widget abs" style="top:1072px">
  <h3>Latest post</h3>
  <div class="mini"><div class="mini-thumb" role="img" aria-label="Security photo" style="background:#2c4f80"></div><div><b>Digital safety notes</b><small>Lorem ipsum is simply dummy text here</small></div></div>
  <div class="mini"><div class="mini-thumb" role="img" aria-label="Family photo" style="background:#9ab06a"></div><div><b>Quiet mind stories</b><small>Lorem ipsum is simply dummy text here</small></div></div>
  <div class="mini" style="margin-bottom:0"><div class="mini-thumb" role="img" aria-label="Desk photo" style="background:#8d8d8d"></div><div><b>Money basics</b><small>Lorem ipsum is simply dummy text here</small></div></div>
</aside>

<aside class="widget abs" style="top:1348px">
  <h3>Subscribe &amp; Follow</h3>
  <div class="socials"><span></span><span></span><span></span><span></span><span></span><span></span><span></span></div>
  <div class="sub"><div class="sub-field">Enter your email</div><div class="sub-btn">Submit</div></div>
</aside>

<aside class="widget abs" style="top:1512px;height:250px">
  <h3>Testimonials</h3>
  <p>Lorem ipsum is simply dummy text of the printing and typesetting industry. Lorem ipsum has been the standard dummy text.</p>
  <div class="author"><div class="author-pic" role="img" aria-label="Portrait of a client"></div><div><b>JAMES ROE</b><small>Business Owner</small></div></div>
</aside>

<footer class="site-footer abs">
  <div class="foot-col"><h4>How we help</h4><ul><li>Preservation consultant</li><li>Stored values audit</li><li>Increase skill insight</li><li>Loss reduction plans</li><li>Partnership reports</li></ul></div>
  <div class="foot-col"><h4>Services</h4><ul><li>Preservation counseling</li><li>On the street team</li><li>Integration and scale</li><li>Migration and execution</li><li>Control of planning</li></ul></div>
  <div class="foot-col"><h4>Support</h4><ul><li>Privacy Policy</li><li>Terms &amp; Condition</li><li>Sitemap</li></ul></div>
  <div class="foot-col"><h4>Tag</h4><div class="tags"><span>Technology</span><span>Blog</span><span>Security</span><span>Support</span><span>Design</span><span>Advertising</span><span>Theme</span><span>Finance</span><span>Kids</span></div></div>
</footer>
<div class="foot-bar abs"><span>Copyright 2016 dorianhelpe • All Rights Reserved</span><div class="foot-social"><span></span><span></span><span></span><span></span><span></span></div></div>

</body>
</html>
```